Home page design for Drone video business (the Business focusses on home videos for realtors)

Dear reader,

*I NEED DESIGNS OF ALL THE PAGES*
We need a first design of a homepage and of 4 other pages of the website of a business that sells drone video services. All the pages will need to be in the similar design style.
The video's are targeted at consumers that want to sell there home and would like to have a cool drone video of photos of their home.

How does the website look:
- has a navbar on top
- A cool looking banner of an areal drone.
- A Big header: with company name: SkyLoftReels
- A smaller subheader: We film your home to increase your chances of sale
- Then a section with a Big header: How does it work
- In this section a place for a vimeo explainitory video
- Then a similar navbar styled bar with a phone number and a email address
- Then a section where the videos porfolio is displayed in a cool way
- Inside this sectiona header: Our work

- A section with header: Why us?
- 4 symbols here with a subheader and some lorum ipsum text underneath (see wireframe images)

- Under that a: Contact us
- where you can put in name, email, phone, message box and a send button

- At the bottom a footer with phone number and a fake address for now.

Be creative. Use creative but serious color.
Use a serious font. Make it a sharp design. Sharp lines. Not to dark design and not to light design.

The wireframes are the same kind of images.
PLEASE PUT IN DESIGNS OF ALL THE PAGES

Good luck

Target Market(s)

People that want to sell home and want to make a cool drone video or photos of their home.

Industry/Entity Type

Business

Contact Information for Business Card

Lucas Wenning
lucas@skyloftreels.example
+31647208351

Logo Text

SkyLoftReels

Number of Pages Required

1 page

Font styles to use
Sans Serif

Requirements
Must have
• All the sections as explained in the instructions.
• The nav bar should have an about us, services, portfolio and a contact us buttons.
• See instruction for details.
• Must include designs of the front page, contact us, our services, portfolio and contact us.
• If you do add some designs for the "about us", "services", "prices", "portfolio" and "contact us" pages, you make a way better chance of winning the competition.
Nice to have
• designs for the other pages as described at the Must haves. You make a better chance of winning if you include them. Look at the wireframes to see the mockups for those pages. think creative about what kind of sections and design should be included in those pages.
Should not have
• bad designs.

```html
<!DOCTYPE html>
<html lang="en">
<head>
<meta charset="utf-8">
<title>SkyLoftReels – Home</title>
<link href="https://fonts.googleapis.com/css2?family=Exo+2:wght@500;600&family=Lato:wght@400;700;900&display=swap" rel="stylesheet">
<style>
  :root {
    --red: #a5161c;
    --red-dark: #8c1015;
    --ink: #2b2b2b;
    --black: #0d0d0d;
    --white: #ffffff;
    --band: #efefef;
    --paper: #e6e4e1;
    --line: #d6d6d6;
    --muted: #bdbdbd;
  }
  * { box-sizing: border-box; margin: 0; padding: 0; }
  html, body { width: 1200px; height: 2539px; overflow: hidden; background: var(--white); }
  body { position: relative; font-family: "Lato", Arial, sans-serif; color: var(--ink); }
  .abs { position: absolute; }

  /* navigation */
  .site-nav { left: 0; top: 0; width: 1200px; height: 64px; background: var(--white); border-bottom: 2px solid #cfd8e0; }
  .brand { left: 98px; top: 18px; font-family: "Exo 2", sans-serif; font-weight: 600; font-size: 24px; color: var(--ink); letter-spacing: 0.5px; }
  .nav-link { top: 0; height: 64px; line-height: 70px; font-weight: 700; font-size: 16px; color: var(--black); text-align: center; }
  .nav-link.is-active { background: var(--red); color: var(--white); border-bottom: 4px solid #1f1f1f; line-height: 66px; }

  /* hero */
  .hero { left: 0; top: 64px; width: 1200px; height: 498px;
    background: linear-gradient(180deg, #3c8fd4 0%, #8fc1e6 30%, #5f9fb6 48%, #2f8f9d 65%, #5d8a60 85%, #8d8f7d 100%); }
  .hero-title { left: 0; width: 1200px; top: 272px; text-align: center; font-weight: 700; font-size: 44px; color: var(--white); text-shadow: 0 2px 6px rgba(0,0,0,.45); letter-spacing: 0.5px; }
  .hero-sub { left: 0; width: 1200px; text-align: center; font-weight: 700; font-size: 30px; color: var(--white); text-shadow: 0 2px 5px rgba(0,0,0,.45); line-height: 39px; top: 332px; }
  .hero-dots { left: 570px; top: 535px; display: flex; gap: 6px; }
  .hero-dots span { width: 10px; height: 10px; border-radius: 50%; background: rgba(255,255,255,.85); }

  /* section headings */
  .section-title { left: 0; width: 1200px; text-align: center; font-family: "Exo 2", sans-serif; font-weight: 600; font-size: 34px; color: var(--ink); }
  .section-title em { font-style: normal; color: var(--red); }

  /* explainer video */
  .explainer { left: 271px; top: 694px; width: 660px; height: 379px; background: linear-gradient(180deg, #1b1b1b 0%, #2d6e9a 45%, #3f8fb8 80%, #e7c7b0 100%); }

  /* contact band */
  .contact-band { left: 0; top: 1073px; width: 1200px; height: 115px; background: var(--band); }
  .band-item { top: 1113px; display: flex; align-items: center; gap: 16px; font-family: "Exo 2", sans-serif; font-weight: 500; font-size: 25px; color: var(--ink); }
  .band-divider { left: 558px; top: 1103px; width: 1px; height: 55px; background: var(--muted); }

  /* portfolio */
  .work-card { top: 1303px; width: 295px; height: 251px; background: var(--white); border: 1px solid var(--line); padding: 8px; }
  .work-thumb { width: 100%; height: 100%; position: relative; }
  .thumb-a { background: linear-gradient(180deg, #3a7fd0 0%, #7fb0e6 45%, #c9b590 70%, #6f7a5a 100%); }
  .thumb-b { background: linear-gradient(180deg, #cfd6de 0%, #b9b8b0 45%, #d8c7a4 70%, #7d7a62 100%); }
  .thumb-c { background: linear-gradient(180deg, #c9d3dd 0%, #8d8272 45%, #6d6154 70%, #e6e9ee 100%); }
  .play-badge { position: absolute; left: 50%; top: 50%; width: 52px; height: 34px; margin: -17px 0 0 -26px; background: var(--red); border-radius: 7px; }
  .play-badge::after { content: ""; position: absolute; left: 21px; top: 10px; border-left: 13px solid var(--white); border-top: 7px solid transparent; border-bottom: 7px solid transparent; }
  .carousel-arrow { top: 1400px; }

  /* why us */
  .why-us { left: 0; top: 1598px; width: 1200px; height: 491px; background: var(--paper); }
  .feature-icon { width: 108px; height: 108px; border-radius: 50%; background: var(--red); border: 4px solid var(--white); box-shadow: 0 0 0 1px #cfcfcf; display: flex; align-items: center; justify-content: center; }
  .feature-title { font-family: "Exo 2", sans-serif; font-weight: 600; font-size: 22px; color: var(--ink); }
  .feature-text { width: 290px; font-size: 12.7px; line-height: 21px; color: var(--ink); }

  /* contact form */
  .field { background: var(--white); border: 1px solid var(--line); font-size: 13px; color: var(--ink); padding: 0 12px; display: flex; align-items: center; }
  .field-message { align-items: flex-start; padding-top: 12px; }
  .submit-btn { left: 537px; top: 2397px; width: 126px; height: 40px; background: var(--red); color: var(--white); font-family: "Exo 2", sans-serif; font-weight: 600; font-size: 16px; display: flex; align-items: center; justify-content: center; }

  /* footer */
  .site-footer { left: 0; top: 2483px; width: 1200px; height: 56px; background: var(--black); border-bottom: 3px solid var(--red); }
  .footer-item { top: 2498px; display: flex; align-items: center; gap: 12px; font-size: 16px; color: var(--white); }
  .copyright { right: 97px; top: 2500px; font-weight: 900; font-size: 12.5px; color: var(--white); }
</style>
</head>
<body>

<header class="abs site-nav">
  <div class="abs brand">SkyLoftReels</div>
  <div class="abs nav-link is-active" style="left:498px;width:96px;">HOME</div>
  <div class="abs nav-link" style="left:618px;width:84px;">SERVICES</div>
  <div class="abs nav-link" style="left:735px;width:94px;">ABOUT US</div>
  <div class="abs nav-link" style="left:860px;width:100px;">PORTFOLIO</div>
  <div class="abs nav-link" style="left:998px;width:112px;">CONTACT US</div>
</header>

<section class="abs hero" role="img" aria-label="Aerial drone photograph of a coastal city with marina and a hovering camera drone"></section>
<h1 class="abs hero-title">SKYLOFTREELS</h1>
<p class="abs hero-sub">WE FILM YOUR HOME TO<br>INCREASE YOUR CHANCES OF SALE</p>
<div class="abs hero-dots"><span></span><span></span><span></span><span></span></div>

<h2 class="abs section-title" style="top:610px;">HOW DOES IT <em>WORK?</em></h2>
<div class="abs explainer" role="img" aria-label="Hands holding a tablet playing the explainer video of a drone over a city"></div>

<div class="abs contact-band"></div>
<div class="abs band-item" style="left:310px;">
  <svg width="30" height="40" viewBox="0 0 24 32"><path d="M6 2 L10 2 L11 9 L8 11 Q9 18 14 23 L17 21 L22 25 L21 30 Q12 31 6 22 Q1 13 6 2Z" fill="var(--red)"/></svg>
  <span>+31647208351</span>
</div>
<div class="abs band-divider"></div>
<div class="abs band-item" style="left:594px;">
  <svg width="48" height="32" viewBox="0 0 48 32"><rect x="1" y="1" width="46" height="30" fill="var(--red)"/><path d="M2 2 L24 18 L46 2 M2 30 L19 14 M46 30 L29 14" stroke="var(--white)" stroke-width="2.5" fill="none"/></svg>
  <span>contact@skyloftreels.example</span>
</div>

<h2 class="abs section-title" style="top:1236px;">OUR <em>WORK?</em></h2>
<svg class="abs carousel-arrow" style="left:42px;" width="32" height="60" viewBox="0 0 32 60"><path d="M30 2 L2 30 L30 58" stroke="#c4c4c4" stroke-width="2" fill="none"/></svg>
<div class="abs work-card" style="left:98px;"><div class="work-thumb thumb-a" role="img" aria-label="Drone pilot flying a drone in front of a suburban house"><span class="play-badge"></span></div></div>
<div class="abs work-card" style="left:454px;"><div class="work-thumb thumb-b" role="img" aria-label="Drone hovering above a stucco family home"><span class="play-badge"></span></div></div>
<div class="abs work-card" style="left:807px;"><div class="work-thumb thumb-c" role="img" aria-label="Drone filming a stone house in winter"><span class="play-badge"></span></div></div>
<svg class="abs carousel-arrow" style="left:1126px;" width="32" height="60" viewBox="0 0 32 60"><path d="M2 2 L30 30 L2 58" stroke="#c4c4c4" stroke-width="2" fill="none"/></svg>

<section class="abs why-us"></section>
<h2 class="abs section-title" style="top:1637px;">WHY <em>US?</em></h2>

<div class="abs feature-icon" style="left:161px;top:1721px;">
  <svg width="56" height="56" viewBox="0 0 56 56" fill="none" stroke="#fff" stroke-width="3"><circle cx="12" cy="12" r="8"/><circle cx="44" cy="12" r="8"/><circle cx="12" cy="44" r="8"/><circle cx="44" cy="44" r="8"/><path d="M17 17 L39 39 M39 17 L17 39"/><rect x="23" y="23" width="10" height="10" fill="#fff"/></svg>
</div>
<div class="abs feature-title" style="left:293px;top:1718px;">CHEAP</div>
<p class="abs feature-text" style="left:293px;top:1755px;">Lorem ipsum dolor sit amet, consectetuer sit al adipiscing elit, sed diam nonummy nibh dolor euismod tincidunt ut laoreet dolore magna sit aliquam erat volutpat.</p>

<div class="abs feature-icon" style="left:625px;top:1721px;">
  <svg width="56" height="56" viewBox="0 0 56 56" fill="none" stroke="#fff" stroke-width="3"><circle cx="16" cy="16" r="10"/><circle cx="40" cy="16" r="10"/><circle cx="16" cy="40" r="10"/><circle cx="40" cy="40" r="10"/><rect x="22" y="22" width="12" height="12" fill="#fff"/></svg>
</div>
<div class="abs feature-title" style="left:760px;top:1718px;">FLEXIBLE</div>
<p class="abs feature-text" style="left:760px;top:1755px;">Lorem ipsum dolor sit amet, consectetuer sit al adipiscing elit, sed diam nonummy nibh dolor euismod tincidunt ut laoreet dolore magna sit aliquam erat volutpat.</p>

<div class="abs feature-icon" style="left:161px;top:1891px;">
  <svg width="56" height="56" viewBox="0 0 56 56" fill="none" stroke="#fff" stroke-width="3"><rect x="6" y="10" width="44" height="30"/><path d="M22 48 L34 48 M28 40 L28 48"/><text x="28" y="31" text-anchor="middle" font-family="Lato, sans-serif" font-weight="900" font-size="15" fill="#fff" stroke="none">4K</text></svg>
</div>
<div class="abs feature-title" style="left:293px;top:1888px;">4K QUALITY</div>
<p class="abs feature-text" style="left:293px;top:1925px;">Lorem ipsum dolor sit amet, consectetuer sit al adipiscing elit, sed diam nonummy nibh dolor euismod tincidunt ut laoreet dolore magna sit aliquam erat volutpat.</p>

<div class="abs feature-icon" style="left:625px;top:1891px;">
  <svg width="60" height="56" viewBox="0 0 60 56" fill="none" stroke="#fff" stroke-width="3"><path d="M4 14 L24 14 M36 14 L56 14 M14 14 L14 22 M46 14 L46 22"/><rect x="14" y="22" width="32" height="12" fill="#fff"/><path d="M20 34 L14 48 M40 34 L46 48 M10 48 L50 48"/></svg>
</div>
<div class="abs feature-title" style="left:760px;top:1893px;">INCREASE SALE CHANCE</div>
<p class="abs feature-text" style="left:760px;top:1928px;">Lorem ipsum dolor sit amet, consectetuer sit al adipiscing elit, sed diam nonummy nibh dolor euismod tincidunt ut laoreet dolore magna sit aliquam erat volutpat.</p>

<h2 class="abs section-title" style="top:2136px;">CONTACT <em>US</em></h2>
<div class="abs field" style="left:124px;top:2209px;width:299px;height:42px;">Name</div>
<div class="abs field" style="left:450px;top:2209px;width:298px;height:42px;">Name</div>
<div class="abs field" style="left:777px;top:2209px;width:298px;height:42px;">Name</div>
<div class="abs field field-message" style="left:124px;top:2275px;width:951px;height:93px;">Message</div>
<div class="abs submit-btn">SUBMIT</div>

<footer class="abs site-footer"></footer>
<div class="abs footer-item" style="left:98px;">
  <svg width="18" height="26" viewBox="0 0 24 32"><path d="M6 2 L10 2 L11 9 L8 11 Q9 18 14 23 L17 21 L22 25 L21 30 Q12 31 6 22 Q1 13 6 2Z" fill="#fff"/></svg>
  <span>+31647208351</span>
</div>
<div class="abs footer-item" style="left:262px;">
  <svg width="26" height="18" viewBox="0 0 48 32"><rect x="1" y="1" width="46" height="30" fill="#fff"/><path d="M2 2 L24 18 L46 2 M2 30 L19 14 M46 30 L29 14" stroke="var(--black)" stroke-width="3" fill="none"/></svg>
  <span>contact@skyloftreels.example</span>
</div>
<div class="abs copyright">COPYRIGHT © 2016 SKYLOFTREELS. ALL RIGHTS RESERVED.</div>

</body>
</html>
```